B2B Case Study Template Design (InDesign or Affinity Designer)

Hello,We are a company specializing in custom sanitary space fit-outs and Solid Surface manufacturing. We are looking for a talented layout designer to create a professional and modern "Case Study" template to showcase our projects.This template must strictly be designed using Adobe InDesign or Affinity Designer. We do not want Canva, Word, or PowerPoint files.Attached, there is a file you can reference named "Brelo - Case Study.pdf". This is our previous layout.

Your mission is to recreate this case study using our new brand guidelines (which I will also provide) while using the exact same texts, photos, and sections (Key Data / "Données clés", Valkor's Role / "Le rôle d'Valkor", Valkor Products / "Produits Valkor").

Note: This project is the first of a series. We want to keep everything in the same project scope moving forward. If the work is satisfactory, we will hire you directly for upcoming print materials (flyer templates, catalogs, etc.).

---
2 Exemples of existing Case Studies : BRELO and TOLVEN
1 Full INDISIGN assembled file for MURESK project (you can work from there)
The logo (multi format)
And a zip file with the PATTERN, FONT and LOGO ALTERNATIVES (for graphic use only - on a photo, or else)

Target Market(s)

Building professionals, architects, specifiers, B2B companies, and contractors.

Industry/Entity Type

Architecture / Construction / B2B

Font styles to use
Sans Serif

Requirements
Must have
• The final source file must be delivered in Adobe InDesign (.indd/.idml) or Affinity Designer format. The design must be clean, structured, and highlight the architectural photography. Paragraph and character styles must be properly set up in the software so we can easily edit the text ourselves in the future. Strict integration of our new brand guidelines (colors, typography).
Nice to have
• A modular design: a layout that works perfectly for a 2-page (front/back) document, but can be easily expanded to 3 or 4 pages if a specific case study requires more content. Layout suggestions for recurring graphic elements (e.g., custom icons for key data, elegant frames for pull quotes).
Should not have
• Do NOT use Canva, Microsoft Word, or Photoshop for the layout. Avoid cluttered, overly colorful, or whimsical designs. We are looking for a premium, high-end, and serious aesthetic suited for the architectural field.

```html
<!DOCTYPE html>
<html lang="fr">
<head>
<meta charset="utf-8">
<title>Norva – Projet Muresk – Étude de cas</title>
<link href="https://fonts.googleapis.com/css2?family=Poppins:wght@300;400;600;700;800&family=Jost:wght@300;400&display=swap" rel="stylesheet">
<style>
  :root{
    --backdrop:#dcdcdc;
    --ink:#1b1b1b;
    --charcoal:#2a2a2a;
    --frame:#161616;
    --paper:#ece9e2;
    --text-soft:#3a3a3a;
    --white:#f7f6f3;
    --olive:#5d6b3f;
    --olive-dark:#3f4a2b;
    --wood:#8b5b36;
    --tile:#d9d6d0;
    --steel:#9a9a9a;
  }
  *{box-sizing:border-box;margin:0;padding:0}
  html,body{width:849px;height:1200px;overflow:hidden;background:var(--backdrop)}
  body{position:relative;font-family:"Poppins",sans-serif;color:var(--ink)}

  .spread,.cover{position:absolute;box-shadow:0 6px 14px rgba(0,0,0,.18)}
  .page{position:absolute;top:0;height:100%;overflow:hidden}
  .photo{position:absolute}

  .photo--washroom{background:linear-gradient(160deg,var(--olive-dark) 0%,var(--olive) 35%,var(--tile) 55%,var(--white) 65%,var(--wood) 82%,#5e3c22 100%)}
  .photo--basin{background:linear-gradient(175deg,var(--olive) 0%,#7a8660 30%,var(--tile) 45%,var(--white) 62%,var(--wood) 78%,#6d4829 100%)}
  .photo--corner{background:linear-gradient(170deg,var(--olive-dark) 0%,var(--olive) 30%,#cfcbc4 52%,var(--white) 62%,var(--wood) 80%,#6a4528 100%)}
  .photo--room{background:linear-gradient(180deg,#6f7b55 0%,var(--olive) 45%,#e4dfdc 70%,#d7d1cf 100%)}

  /* ---------- Row 1 : opening spread + cover ---------- */
  .spread--intro{left:22px;top:150px;width:524px;height:199px;background:var(--charcoal)}
  .spread--intro .page--photo{left:0;width:262px;background:var(--white)}
  .spread--intro .page--photo .photo{left:10px;top:10px;right:10px;bottom:10px}
  .spread--intro .page--data{left:262px;width:262px;background:var(--charcoal);color:var(--white);padding:14px 16px}
  .data__title{font-weight:800;font-size:9px;letter-spacing:.02em;text-transform:uppercase;line-height:1.1}
  .data__lead{font-family:"Jost",sans-serif;font-weight:300;font-size:8px;line-height:1.2;margin-bottom:6px}
  .data__label{font-family:"Jost",sans-serif;font-size:6.5px;text-transform:uppercase;margin:4px 0 2px}
  .data__list{list-style:none;font-size:4.3px;line-height:1.5;font-weight:300}
  .data__list b{font-weight:600}
  .data__note{font-size:4.3px;line-height:1.45;font-weight:300;margin-top:4px;width:150px}
  .data__note b{font-weight:600}
  .products{position:absolute;left:16px;bottom:12px;display:flex;align-items:center;gap:6px}
  .products__label{font-family:"Jost",sans-serif;font-size:6px;text-transform:uppercase;margin-right:4px}
  .products__item{width:20px;height:20px;border-radius:50%;background:radial-gradient(circle at 40% 35%,#f4f4f4,var(--steel))}

  .cover{left:566px;top:150px;width:262px;height:199px;background:var(--charcoal);color:var(--white)}
  .cover .photo{left:0;top:14px;width:128px;bottom:14px}
  .cover__mark{position:absolute;left:142px;top:18px;font-weight:700;font-size:34px;line-height:1.02;letter-spacing:.28em}
  .cover__title{position:absolute;left:142px;top:122px;font-weight:800;font-size:11px;letter-spacing:.02em}
  .cover__subtitle{position:absolute;left:142px;top:138px;font-family:"Jost",sans-serif;font-weight:300;font-size:7.5px;line-height:1.35;letter-spacing:.04em;text-transform:uppercase}

  /* ---------- Framed spreads ---------- */
  .spread--framed{left:84px;width:683px;height:259px;background:var(--frame);padding:5px}
  .spread--framed .page{top:5px;height:249px}
  .page--left{left:5px;width:336px;background:var(--paper)}
  .page--right{left:342px;width:336px;background:var(--paper)}
  .spread--challenge{top:533px}
  .spread--furniture{top:878px}

  .brand-name{font-weight:700;font-size:22px;letter-spacing:.22em;line-height:1}
  .heading-light{font-family:"Jost",sans-serif;font-weight:300;text-transform:uppercase;color:var(--ink)}
  .heading-bold{font-weight:800;font-size:8.5px;text-transform:uppercase;letter-spacing:.01em}
  .body{font-size:4.3px;line-height:1.6;font-weight:300;color:var(--text-soft)}
  .body b{font-weight:600;color:var(--ink)}

  .challenge{position:absolute;left:44px;top:68px;width:250px}
  .challenge .heading-light.h1{font-size:8.2px;margin-top:8px}
  .challenge .heading-light.h2{font-size:5.4px;margin-top:7px}
  .challenge .intro{margin-top:8px}
  .challenge__cols{display:flex;gap:14px;margin-top:8px}
  .challenge__col{flex:1}
  .challenge__col h3{font-family:"Jost",sans-serif;font-weight:400;font-size:5.6px;text-transform:uppercase;margin-bottom:6px}
  .challenge__col p+p{margin-top:5px}
  .spread--challenge .page--right .photo{inset:0}

  .spread--furniture .page--left .photo--corner{left:0;top:0;width:138px;height:100%}
  .furniture{position:absolute;left:160px;top:22px;width:72px}
  .furniture .heading-light{font-size:6.6px;line-height:1.25}
  .furniture .small{font-size:4.6px;line-height:1.3;margin-top:10px}
  .furniture .body{margin-top:10px}
  .furniture .body p+p{margin-top:6px}
  .drawing{position:absolute;left:240px;top:22px;width:80px;height:214px;background:linear-gradient(180deg,#e7e4dd,#dcd8d0);border:1px solid #cfcac1}

  .process{position:absolute;left:16px;top:22px;width:140px}
  .process .heading-light{font-size:6.8px}
  .process .sub{font-size:5px;margin-top:8px;line-height:1.3}
  .process .lead{margin-top:8px;font-weight:600;color:var(--ink)}
  .process ul{list-style:none;margin-top:6px}
  .process li{margin-top:5px}
  .process li::before{content:"• ";color:var(--ink)}
  .process hr{border:0;border-top:1px solid #cfcac1;margin:6px 0}
  .process__cols{display:flex;gap:8px;margin-top:4px}
  .process__cols .body{flex:1}
  .plan-caption{position:absolute;left:170px;top:25px;font-size:4px;color:var(--text-soft)}
  .spread--furniture .page--right .photo--room{left:170px;top:34px;width:140px;height:88px}
  .pattern-field{position:absolute;left:170px;top:130px;width:140px;height:106px;background:linear-gradient(135deg,#e4e0d8,#d8d3ca)}
</style>
</head>
<body>

<!-- Opening spread -->
<section class="spread spread--intro">
  <div class="page page--photo">
    <div class="photo photo--washroom" role="img" aria-label="Photo d'un bloc sanitaire rénové : vasque blanche, meuble en bois et murs vert olive"></div>
  </div>
  <div class="page page--data">
    <p class="data__title">Projet Muresk:</p>
    <p class="data__lead">quand la performance s'adapte<br>à la continuité de service</p>
    <p class="data__label">Données clé</p>
    <ul class="data__list">
      <li><b>Lieu:</b> 12 rue Halden, Paris 17e (Immeuble bureaux Premium)</li>
      <li><b>Maître d'ouvrage:</b> Caldera</li>
      <li><b>Livraison:</b> 2024</li>
    </ul>
    <p class="data__label">Le rôle d'Valkor</p>
    <ul class="data__list">
      <li>Conception de mobilier Orlin sur-mesure</li>
      <li>Planification de la pose par tranches</li>
      <li>Installation en mode «Discret»</li>
    </ul>
    <p class="data__note"><b>L'enjeu majeur du chantier Muresk résidait dans</b> l'environnement immédiat des open spaces occupés, exigeant une discrétion absolue pendant la transformation.</p>
    <div class="products">
      <span class="products__label">Produits Valkor</span>
      <span class="products__item" role="img" aria-label="Produit : robinet"></span>
      <span class="products__item" role="img" aria-label="Produit : distributeur"></span>
      <span class="products__item" role="img" aria-label="Produit : sèche-mains"></span>
    </div>
  </div>
</section>

<!-- Cover -->
<section class="cover">
  <div class="photo photo--basin" role="img" aria-label="Photo de couverture : double vasque blanche sur meuble en bois"></div>
  <p class="cover__mark">NO<br>RVA</p>
  <p class="cover__title">PROJET MURESK</p>
  <p class="cover__subtitle">L'art de l'agilité:<br>rénovation sanitaire<br>en site occupé</p>
</section>

<!-- Challenge spread -->
<section class="spread spread--framed spread--challenge">
  <div class="page page--left">
    <div class="challenge">
      <p class="brand-name">NORVA</p>
      <p class="heading-light h1">Une prouesse d'agilité: le défi du site occupé</p>
      <p class="heading-light h2">Maintenir le confort des usagers pendant la mutation des espaces.</p>
      <div class="body intro">
        <p><b>L'enjeu majeur du chantier Muresk résidait dans l'environnement immédiat:</b></p>
        <p>des open spaces occupés par des collaborateurs en plein travail.<br>Ce projet « Muresk » exigeait donc une discrétion absolue et une rapidité d'exécution chirurgicale.</p>
      </div>
      <div class="challenge__cols">
        <div class="challenge__col body">
          <h3>1. Mode «discret» &amp; propreté:</h3>
          <p>Travailler dans le silence et sans dégagement de poussière était une condition non négociable.</p>
          <p>Valkor a mis en place un protocole spécifique pour garantir une propreté absolue des parties communes et des sanitaires, permettant aux occupants de continuer leurs activités sans nuisance.</p>
        </div>
        <div class="challenge__col body">
          <h3>2. Flux de travail «chrono»</h3>
          <p>Pour éviter la fermeture simultanée de tous les sanitaires de l'immeuble, Valkor a orchestré une pose par tranches successives.</p>
          <p>Ce phasage dynamique a permis de maintenir la continuité de service pour le client tout en assurant un temps de travaux record par étage.</p>
        </div>
      </div>
    </div>
  </div>
  <div class="page page--right">
    <div class="photo photo--basin" role="img" aria-label="Photo d'une double vasque blanche sur meuble bois, murs vert olive et miroir"></div>
  </div>
</section>

<!-- Furniture & process spread -->
<section class="spread spread--framed spread--furniture">
  <div class="page page--left">
    <div class="photo photo--corner" role="img" aria-label="Photo d'une vasque d'angle avec sèche-mains noir et meuble bois"></div>
    <div class="furniture">
      <p class="heading-bold">Mobilier Orlin:</p>
      <p class="heading-light">L'intelligence du sur-mesure</p>
      <p class="heading-light small">S'adapter à l'existant sans compromis sur le design.</p>
      <p class="heading-light small">Le projet Muresk a nécessité une adaptation rare de notre gamme de supports de fixation.</p>
      <div class="body">
        <p><b>Profondeurs atypiques:</b><br>Le bureau d'études Valkor a redessiné le mobilier ORLINSOL pour répondre à des profondeurs de niches sortant des standards habituels, optimisant ainsi chaque centimètre carré d'espace.</p>
        <p>De plus, la redéfinition du support a permis l'ajout de rangements sous-jacents, permettant le stockage de matériel d'entretien, etc.</p>
      </div>
    </div>
    <div class="drawing" role="img" aria-label="Plans techniques et vue 3D du meuble vasque sur-mesure"></div>
  </div>
  <div class="page page--right">
    <div class="process">
      <p class="heading-bold">De la conception à la pose:</p>
      <p class="heading-light">La maîtrise de A à Z</p>
      <p class="heading-light sub">Une responsabilité totale pour<br>un résultat garanti.</p>
      <p class="body lead">Au-delà de la technique, ce projet représente également comment la société Valkor prend la responsabilité du résultat final en assurant elle-même la pose de ses produits.</p>
      <ul class="body">
        <li><b>Manutention maîtrisée:</b> Une logistique invisible en milieu occupé. Livraison et acheminement sans perturber les flux de l'immeuble, en dehors des pics d'affluence.</li>
        <li><b>Précision de pose:</b> L'ingénierie face aux contraintes de la rénovation. Ajustement des structures sur-mesure sur des supports existants parfois irréguliers &amp; redimensionnement du mobilier Orlin.</li>
      </ul>
      <hr>
      <p class="body"><b>• Engagement rapidité: un phasage précis pour la continuité de service</b></p>
      <div class="process__cols">
        <p class="body">L'installation a été orchestrée par tranches successives pour éviter la fermeture simultanée de tous les points d'eau. Grâce à un pré-montage en atelier de Haut-Vellan, le temps d'intervention</p>
        <p class="body">physique sur le site de Muresk a été réduit au strict minimum. Chaque journée s'est conclue par un nettoyage rigoureux «fin de poste», sans poussière ni nuisances.</p>
      </div>
    </div>
    <p class="plan-caption">RS - Muresk 1 - Femmes</p>
    <div class="photo photo--room" role="img" aria-label="Photo cotée d'un mur de sanitaire avant pose, murs vert olive et carrelage clair"></div>
    <div class="pattern-field" role="img" aria-label="Motif graphique de la marque en répétition"></div>
  </div>
</section>

</body>
</html>
```